Logo & Visitenkarte für Weinbauer
Zielgruppe
Ich bin Weinbauer und betreibe auch einen Buschenschank. Zielgruppe ist die Gastronomie und der (Durchschnitts-) Endverbraucher.
Aufgabenstellung
Unsere Betriebsstätte ist im Rebhügelgau Weinviertel (Österreich).
Wir wollen die Werte Tradition, Regional, Vertrauen und Bodenständigkeit vermitteln.
Unsere Kunden schätzen die Herkunft.
Das Logo soll als Firmenlogo und auch für die Weinetiketten verwendet werden können.

```html
<!DOCTYPE html>
<html lang="de">
<head>
<meta charset="utf-8">
<title>Brunnhofer Weinetiketten</title>
<link rel="stylesheet" href="https://fonts.googleapis.com/css2?family=Raleway:wght@300;400&display=swap">
<style>
  :root {
    --canvas: #ffffff;
    --ink: #1a1a1a;
    --granat: #b3192a;
    --granat-paper: #ebe8ea;
    --chardonnay: #3ea535;
    --chardonnay-paper: #fdfcfa;
    --turmalin: #c96e52;
    --turmalin-paper: #fbefe9;
  }
  * { margin: 0; padding: 0; box-sizing: border-box; }
  html, body {
    width: 1200px;
    height: 1200px;
    overflow: hidden;
    background: var(--canvas);
  }
  .label-set {
    width: 1200px;
    height: 1200px;
    display: flex;
    justify-content: center;
    align-items: center;
    gap: 60px;
  }
  .wine-label {
    width: 300px;
    height: 570px;
    display: flex;
    flex-direction: column;
    align-items: center;
    padding-top: 50px;
    font-family: 'Raleway', sans-serif;
    box-shadow: 0 0 0 1px rgba(0,0,0,0.06);
  }
  .wine-label--granat { background: var(--granat-paper); --accent: var(--granat); }
  .wine-label--chardonnay { background: var(--chardonnay-paper); --accent: var(--chardonnay); }
  .wine-label--turmalin { background: var(--turmalin-paper); --accent: var(--turmalin); }

  .brand-mark {
    width: 170px;
    height: 170px;
    border-radius: 50%;
    background: var(--accent);
  }
  .brand-name {
    margin-top: 100px;
    font-size: 38px;
    font-weight: 400;
    line-height: 1.1;
    color: var(--ink);
    white-space: nowrap;
  }
  .brand-tagline {
    margin-top: 4px;
    font-size: 16px;
    font-weight: 400;
    color: var(--ink);
    white-space: nowrap;
    font-variant-numeric: oldstyle-nums;
  }
  .wine-name {
    margin-top: 62px;
    font-size: 22px;
    font-weight: 400;
    color: var(--accent);
    text-transform: uppercase;
    white-space: nowrap;
  }
</style>
</head>
<body>
  <main class="label-set">
    <section class="wine-label wine-label--granat">
      <div class="brand-mark"></div>
      <p class="brand-name">Brunnhofer</p>
      <p class="brand-tagline">Weinbau seit 1947</p>
      <p class="wine-name">Cuvee Granat</p>
    </section>
    <section class="wine-label wine-label--chardonnay">
      <div class="brand-mark"></div>
      <p class="brand-name">Brunnhofer</p>
      <p class="brand-tagline">Weinbau seit 1947</p>
      <p class="wine-name">Chardonnay</p>
    </section>
    <section class="wine-label wine-label--turmalin">
      <div class="brand-mark"></div>
      <p class="brand-name">Brunnhofer</p>
      <p class="brand-tagline">Weinbau seit 1947</p>
      <p class="wine-name">Rosé Turmalin</p>
    </section>
  </main>
</body>
</html>
```